All-Natural Head Lice Removal company

I need a business card with my pre-existing logo. We are a new company located in Portland Oregon that goes into peoples homes to help with head lice removal. My products and approach are all- natural and also will be around children.On my current logo we used Teal Bl and the color Green. I am open to new ideas just want it simple and creative

Target Market(s)

my biggest market is families of school aged children

Industry/Entity Type

Business

Contact Information for Business Card

see upload for details from previous business card

Font styles to use
Serif

Colors
33a6d7
9bcb3b
f37122

Requirements
Must have
• Basic information/ logo put into a creative format that is catching to the eye
Nice to have
• creative

```html
<!DOCTYPE html>
<html lang="en">
<head>
<meta charset="utf-8">
<title>Nit Free Home – Business Card</title>
<link href="https://fonts.googleapis.com/css2?family=Comic+Neue:wght@400;700&display=swap" rel="stylesheet">
<style>
  :root{
    --bg:#ecebe7;
    --card:#ffffff;
    --green:#8cc63f;
    --green-dark:#6fae2c;
    --green-light:#a9d85c;
    --teal:#33a6d7;
    --ink:#2b2b2b;
    --muted:#666666;
    --white:#ffffff;
  }
  *{box-sizing:border-box;margin:0;padding:0}
  html,body{width:1200px;height:843px;overflow:hidden}
  body{
    background:var(--bg);
    font-family:"Comic Neue",cursive;
    position:relative;
  }
  .card{
    position:absolute;
    top:267px;
    width:540px;
    height:309px;
    border-radius:22px;
    background:var(--card);
    overflow:hidden;
    box-shadow:0 6px 18px rgba(0,0,0,.18);
  }
  .card--back{left:40px}
  .card--front{left:620px}

  /* back side */
  .back-art{
    position:absolute;
    left:24px;top:34px;
    width:130px;height:240px;
    border-radius:65px 65px 14px 14px;
    background:linear-gradient(180deg,#dcebd0 0%,#e3eff6 55%,#f4f4f4 100%);
    opacity:.75;
  }
  .back-text{
    position:absolute;
    right:30px;top:122px;
    width:330px;
    text-align:right;
    color:var(--muted);
    font-size:15px;
    line-height:1.4;
  }

  /* front side */
  .front-band{
    position:absolute;inset:0;
    width:100%;height:100%;
  }
  .holder{
    position:absolute;left:28px;top:26px;color:var(--white);
  }
  .holder__name{font-weight:700;font-size:24px;letter-spacing:.5px}
  .holder__title{font-size:16px;margin-top:2px}
  .contact{
    position:absolute;left:28px;top:190px;
    list-style:none;color:var(--white);font-size:16px;font-weight:700;
  }
  .contact li{display:flex;align-items:center;gap:8px;margin-bottom:6px}
  .contact svg{width:14px;height:14px;flex:none}
  .magnifier-art{
    position:absolute;left:300px;top:34px;
    width:150px;height:150px;
    border-radius:50%;
    background:linear-gradient(135deg,#9fd3ec 0%,#8cc63f 100%);
  }
  .brand{
    position:absolute;right:26px;bottom:40px;
    display:flex;align-items:center;gap:10px;
  }
  .brand__dot{width:34px;height:34px;border-radius:50%;background:var(--green)}
  .brand__name{font-weight:700;font-size:24px;color:var(--ink)}
</style>
</head>
<body>

<section class="card card--back" aria-label="Card back">
  <div class="back-art" role="img" aria-label="Faint magnifying glass illustration"></div>
  <p class="back-text">Try Nit Free Home Today, Be Lice Free Tomorrow!<br>All Natural Head Lice Removal Services</p>
</section>

<section class="card card--front" aria-label="Card front">
  <svg class="front-band" viewBox="0 0 540 309" preserveAspectRatio="none" aria-hidden="true">
    <defs>
      <linearGradient id="bandFill" x1="0" y1="0" x2="1" y2="1">
        <stop offset="0" stop-color="#a9d85c"/>
        <stop offset="1" stop-color="#6fae2c"/>
      </linearGradient>
    </defs>
    <path d="M0 0 H330 C300 120 300 200 290 309 H0 Z" fill="url(#bandFill)"/>
  </svg>

  <div class="holder">
    <p class="holder__name">Mara Jennings</p>
    <p class="holder__title">Owner</p>
  </div>

  <ul class="contact">
    <li>
      <svg viewBox="0 0 24 24" fill="#fff"><path d="M6.6 10.8a15 15 0 0 0 6.6 6.6l2.2-2.2c.3-.3.7-.4 1-.2 1.1.4 2.3.6 3.6.6.6 0 1 .4 1 1V20c0 .6-.4 1-1 1A17 17 0 0 1 3 4c0-.6.4-1 1-1h3.5c.6 0 1 .4 1 1 0 1.3.2 2.5.6 3.6.1.3 0 .7-.2 1z"/></svg>
      1-855-555-NITS (6487)
    </li>
    <li>
      <svg viewBox="0 0 24 24" fill="#fff"><path d="M2 5h20v14H2z M2 5l10 8 10-8" stroke="#8cc63f" stroke-width="1.5"/></svg>
      mara@nitfreehome.com
    </li>
    <li>
      <svg viewBox="0 0 24 24" fill="none" stroke="#fff" stroke-width="2"><circle cx="12" cy="12" r="10"/><path d="M2 12h20M12 2c3 3 3 17 0 20M12 2c-3 3-3 17 0 20"/></svg>
      www.nitfreehome.com
    </li>
  </ul>

  <div class="magnifier-art" role="img" aria-label="Illustrated magnifying glass over a green eye"></div>

  <div class="brand">
    <span class="brand__dot"></span>
    <span class="brand__name">Nit Free Home</span>
  </div>
</section>

</body>
</html>
```